Software Platform User Guide (Manual)

We need a user manual template for our online e-learning platform, Lanthorn, which allows users to create their own online courses.

We’re looking for a template for a few pages, including a cover, back page, table of contents, and pages for text-only (or bullet points), and text & images (screenshots). We would like to be able to add new pages and adjust textual content ourselves. Lorem ipsum is totally cool as placeholder text. The name of the product is Lanthorn, but the company name is Cordwain Meridian, so we would like the cover and back cover to say “Cordwain Meridian" and "Lanthorn".

We have uploaded a few files to give you a sense of our color scheme and logo. You can also check out our website at cmvista.example for an idea of our aesthetic sensibility. The design should be simple and elegant, and (being a user manual) clarity is king. We use Avenir and Elizabeth as or primary fonts. We have also uploaded some sample screen shots from Lanthorn. You can use those screenshots to help direct your work, but note that the interface design is changing soon; i.e., you should emphasize the Cordwain Meridian brand aesthetic more so than the Lanthorn user interface design.

Target Market(s)

Businesses and nonprofits looking to implement our platform. Many buyers are female, but the people reading the manual are typically male.

Industry/Entity Type

It Company

Requirements
Must have
• The final product must be a template that will work in Microsoft Word, PowerPoint, or Apple Keynote/Pages. It's fine to send PDFs for previews. Note we need the final product in ONE of the above choices (Word, Powerpoint, Keynote, or Pages), not ALL.

You must make use of the CM logo and fonts on every page. Note that the tag line, "quickest bridge across two shores of thought" in one version of the logo does note have to be included.

We need clear delineation between headers, sub-headers, and bullets, as well as a great looking cover, table of contents and back page.

Please Note: Please disregard the OLUD logo on any screenshots. These were mockups for a client. Please don't use the OLUD name or logo.

```html
<!DOCTYPE html>
<html lang="en">
<head>
<meta charset="utf-8">
<title>Lanthorn User Guide — Cover</title>
<link rel="stylesheet" href="https://fonts.googleapis.com/css2?family=Tinos:wght@400&display=swap">
<style>
  :root {
    --navy: #1f3f5c;
    --lime: #b5d334;
    --sky: #4a8acb;
    --paper: #ffffff;
    --ink: #3a3f45;
    --photo-light: #f1f2f3;
    --photo-mid: #b9bec4;
  }
  html, body {
    margin: 0;
    padding: 0;
    width: 809px;
    height: 1200px;
    overflow: hidden;
    background: var(--navy);
  }
  .cover {
    position: relative;
    width: 809px;
    height: 1200px;
    overflow: hidden;
    background: var(--navy);
    font-family: "Tinos", "Times New Roman", serif;
  }
  .cover__curves {
    position: absolute;
    inset: 0;
    width: 809px;
    height: 1200px;
  }
  .brand-mark {
    position: absolute;
    left: 89px;
    top: 85px;
    width: 188px;
    height: 188px;
    border-radius: 50%;
    background: var(--lime);
    display: flex;
    align-items: center;
    justify-content: center;
    color: var(--paper);
    font-size: 72px;
    line-height: 1;
  }
  .company-name {
    position: absolute;
    left: 334px;
    top: 140px;
    margin: 0;
    font-weight: 400;
    font-size: 37px;
    line-height: 1;
    color: var(--lime);
    white-space: nowrap;
  }
  .tagline {
    position: absolute;
    left: 335px;
    top: 197px;
    margin: 0;
    font-size: 15.5px;
    letter-spacing: 1.6px;
    color: var(--paper);
    white-space: nowrap;
  }
  .product-name {
    position: absolute;
    left: 0;
    width: 1052px;
    top: 348px;
    margin: 0;
    text-align: center;
    font-weight: 400;
    font-size: 56px;
    letter-spacing: 5px;
    line-height: 1;
    color: var(--sky);
  }
  .hero-photo {
    position: absolute;
    left: 120px;
    top: 440px;
    width: 686px;
    height: 480px;
    border-radius: 12px;
    background: radial-gradient(ellipse at 50% 55%, var(--photo-mid) 0%, var(--photo-light) 62%, var(--paper) 100%);
  }
  .web-address {
    position: absolute;
    left: 342px;
    top: 1041px;
    display: flex;
    align-items: center;
    gap: 30px;
  }
  .web-address__dot {
    width: 52px;
    height: 52px;
    border-radius: 50%;
    background: var(--sky);
  }
  .web-address__text {
    font-size: 24px;
    letter-spacing: 3.5px;
    color: var(--ink);
    white-space: nowrap;
  }
  .web-address__domain {
    color: var(--sky);
  }
</style>
</head>
<body>
  <main class="cover">
    <svg class="cover__curves" viewBox="0 0 908 1291" preserveAspectRatio="none" aria-hidden="true">
      <ellipse cx="628" cy="883" rx="572" ry="575" fill="var(--lime)"/>
      <ellipse cx="648" cy="883" rx="562" ry="567" fill="var(--paper)"/>
    </svg>

    <div class="brand-mark">CM</div>
    <h1 class="company-name">Cordwain Meridian</h1>
    <p class="tagline">quickest bridge across two shores of thought</p>

    <h2 class="product-name">Lanthorn</h2>

    <div class="hero-photo" role="img" aria-label="Photo of an open laptop with a hand reaching out of the screen holding a white card"></div>

    <div class="web-address">
      <span class="web-address__dot"></span>
      <span class="web-address__text">www. <span class="web-address__domain">cmvista</span>.example</span>
    </div>
  </main>
</body>
</html>
```